Wordpress Design Project (Nerith)

We need a wordpress design for an established auction and real estate company based in Pennsylvania. The winning design will incorporate a professional layout with and company logo in a very simple and clean layout.

Industry/Entity Type

Real Estate

Requirements
Must have
• Navigation:
1) Home; 2) Auctions; 3) Appraisals; 4) Real Estate; 5) FAQ; 6) About Us; 7) Contact Us.

Site will have overall layout of https://www.plumvarro.com/featured/regions/the-northeast. Home page will have logo and navigation at top. The navigation bar will also have social media icons (facebook, Google+, RSS, twitter) inside it. There will be text in the content area - use lorem ipsum. The image attached will be used below text (auctions.jpg) . Footer will have smaller company loogo, the attached affiliation logos and social media icons.

Logo attached. Color scheme will be black, gray, and red as accent color.
Nice to have
• navigation will have dropdowns, nice to have one represented - under auctions 'All Auctions' will be dropdown.

```html
<!DOCTYPE html>
<html lang="en">
<head>
<meta charset="utf-8">
<title>Nerith — Auctioneers &amp; Appraisers</title>
<link rel="stylesheet" href="https://fonts.googleapis.com/css2?family=Roboto+Condensed:wght@400;700&family=Open+Sans:wght@400;600&display=swap">
<style>
  :root{
    --bg:#232323;
    --bg-deep:#1a1a1a;
    --bar:#111111;
    --nav-active:#2c2c2c;
    --card:#161616;
    --panel:#1c1c1c;
    --text:#e6e6e6;
    --muted:#8a8a8a;
    --soft:#b5b5b5;
    --red:#e03a2a;
    --red-soft:#f0533f;
    --icon:#5a5a5a;
    --band:#f2f2f2;
  }
  *{box-sizing:border-box;margin:0;padding:0}
  html,body{width:1200px;height:2365px;overflow:hidden;background:var(--bg);color:var(--text);font-family:"Open Sans",Arial,sans-serif}
  .page{position:relative;width:1200px;height:2365px}

  .site-header{position:absolute;top:0;left:0;width:1200px;height:102px;background:var(--bg)}
  .brand{position:absolute;left:180px;top:22px;display:flex;align-items:center;gap:12px}
  .brand-mark{width:56px;height:56px;background:var(--red)}
  .brand-name{font-family:"Roboto Condensed",Arial,sans-serif;font-weight:700;font-size:40px;color:#d9d9d9;letter-spacing:1px}
  .social{position:absolute;right:180px;top:36px;display:flex;align-items:center;gap:8px}
  .social-label{font-family:"Roboto Condensed",Arial,sans-serif;font-size:11px;line-height:14px;color:var(--soft);text-align:right;margin-right:6px}
  .social-dot{width:28px;height:28px;border-radius:50%;background:var(--icon)}

  .main-nav{position:absolute;top:102px;left:0;width:1200px;height:43px;background:var(--bar)}
  .main-nav ul{list-style:none;display:flex;margin-left:180px;height:43px}
  .main-nav li{font-family:"Roboto Condensed",Arial,sans-serif;font-size:14px;color:#d0d0d0;text-transform:uppercase;line-height:43px;padding:0 32px}
  .main-nav li.active{background:var(--nav-active)}

  .hero{position:absolute;top:145px;left:0;width:1200px;height:442px;background:linear-gradient(180deg,#3a5a8c 0%,#4e5f7a 30%,#8a6a3a 55%,#c4843a 72%,#4a3a2a 100%)}
  .hero-caption{position:absolute;left:180px;top:339px;width:628px;height:78px;background:rgba(20,20,20,.82);display:flex;align-items:center}
  .hero-title{font-family:"Roboto Condensed",Arial,sans-serif;font-weight:700;font-size:44px;color:var(--red);width:180px;padding-left:28px;border-right:1px solid #444;height:56px;line-height:56px}
  .hero-text{font-size:8.5px;line-height:15px;color:#cfcfcf;text-transform:uppercase;padding:0 22px}
  .hero-arrows{position:absolute;left:808px;top:339px;width:43px}
  .hero-arrow{width:43px;height:38px;background:var(--red-soft);display:flex;align-items:center;justify-content:center;margin-bottom:2px}

  .listings{position:absolute;top:613px;left:180px;width:842px;display:grid;grid-template-columns:407px 407px;column-gap:28px;row-gap:18px}
  .listing{background:var(--card);height:274px;padding:9px}
  .listing-photo{height:194px}
  .listing-title{font-family:"Roboto Condensed",Arial,sans-serif;font-size:13.5px;color:#e0e0e0;text-transform:uppercase;margin:21px 0 0 0}
  .listing-meta{display:flex;justify-content:space-between;align-items:center;margin-top:9px;font-size:8.5px;color:var(--muted)}
  .listing-place{display:flex;align-items:center;gap:6px;color:var(--red)}

  .newsletter{position:absolute;top:2085px;left:180px;width:842px;height:107px;background:var(--panel);display:flex;align-items:center}
  .newsletter-copy{padding-left:33px;width:480px}
  .newsletter-title{font-family:"Roboto Condensed",Arial,sans-serif;font-size:27px;color:var(--red);text-transform:uppercase}
  .newsletter-sub{font-family:"Roboto Condensed",Arial,sans-serif;font-size:20px;color:#bdbdbd;text-transform:uppercase;margin-top:4px}
  .newsletter-form{display:flex;align-items:center;gap:17px;margin-left:5px}
  .fields{display:flex;flex-direction:column;gap:9px}
  .field{width:195px;height:24px;background:#2b2b2b;font-size:8px;color:var(--soft);padding-left:11px;line-height:24px;text-transform:uppercase}
  .subscribe{width:120px;height:30px;background:var(--red-soft);color:#fff;font-size:10px;display:flex;align-items:center;justify-content:center;gap:12px;text-transform:uppercase}

  .affiliations{position:absolute;top:2205px;left:180px;width:842px;height:63px;background:var(--band);display:flex;justify-content:space-around;align-items:center;padding:0 20px}
  .badge{width:72px;height:46px;background:#d6d6d6}
  .badge.round{width:48px;border-radius:50%}

  .site-footer{position:absolute;top:2287px;left:0;width:1200px;height:78px;background:var(--bg-deep);text-align:center}
  .footer-nav{list-style:none;display:flex;justify-content:center;padding-top:22px;font-size:8px;color:#bbb;text-transform:uppercase}
  .footer-nav li{padding:0 14px;border-left:1px solid #555}
  .footer-nav li:first-child{border-left:0}
  .copyright{font-size:7.5px;color:var(--muted);margin-top:10px;text-transform:uppercase}
</style>
</head>
<body>
<div class="page">
  <header class="site-header">
    <div class="brand"><div class="brand-mark"></div><span class="brand-name">Nerith</span></div>
    <div class="social">
      <div class="social-label">CONNECT TO<br>OUR SOCIAL NETWORK :</div>
      <span class="social-dot"></span><span class="social-dot"></span><span class="social-dot"></span><span class="social-dot"></span>
    </div>
  </header>

  <nav class="main-nav">
    <ul>
      <li class="active">Home</li><li>Auctions</li><li>Appraisals</li><li>Real Estate</li><li>FAQ</li><li>About Us</li><li>Contact Us</li>
    </ul>
  </nav>

  <section class="hero" role="img" aria-label="Large Mediterranean-style villa lit up at dusk with palm trees and a fountain">
    <div class="hero-caption">
      <div class="hero-title">NERITH</div>
      <p class="hero-text">All the lorem ipsum generators on the internet tend to repeat predefined chunks as necessary, making this the first true generator on the internet. It uses a dictionary of over 200 Latin words, combined with a handful of model sentence structures...</p>
    </div>
    <div class="hero-arrows">
      <div class="hero-arrow"><svg width="12" height="16" viewBox="0 0 12 16"><path d="M3 2l6 6-6 6" fill="none" stroke="#fff" stroke-width="1.6"/></svg></div>
      <div class="hero-arrow"><svg width="12" height="16" viewBox="0 0 12 16"><path d="M9 2L3 8l6 6" fill="none" stroke="#fff" stroke-width="1.6"/></svg></div>
    </div>
  </section>

  <main class="listings">
    <article class="listing"><div class="listing-photo" role="img" aria-label="Stacked wooden cabinet doors with yellow auction tags" style="background:linear-gradient(135deg,#c9b7a6,#6a2a22 55%,#3a1a16)"></div><h3 class="listing-title">Finding the property you want</h3><div class="listing-meta"><span>Homes for sale, apartments for rent, and property records</span><span class="listing-place"><svg width="7" height="10" viewBox="0 0 7 10"><path d="M3.5 0A3.5 3.5 0 0 0 0 3.5C0 6 3.5 10 3.5 10S7 6 7 3.5A3.5 3.5 0 0 0 3.5 0z" fill="#888"/></svg>Brooklandville, MD</span></div></article>
    <article class="listing"><div class="listing-photo" role="img" aria-label="Bathroom vanities with granite tops and sinks" style="background:linear-gradient(160deg,#d8d8d8,#6c5a4a 50%,#a0602e)"></div><h3 class="listing-title">Finding the property you want</h3><div class="listing-meta"><span>Homes for sale, apartments for rent, and property records</span><span class="listing-place"><svg width="7" height="10" viewBox="0 0 7 10"><path d="M3.5 0A3.5 3.5 0 0 0 0 3.5C0 6 3.5 10 3.5 10S7 6 7 3.5A3.5 3.5 0 0 0 3.5 0z" fill="#888"/></svg>Brooklandville, MD</span></div></article>
    <article class="listing"><div class="listing-photo" role="img" aria-label="Rolls of carpet with yellow tags" style="background:linear-gradient(135deg,#8a8070,#b9b0a0 50%,#6a7078)"></div><h3 class="listing-title">Finding the property you want</h3><div class="listing-meta"><span>Homes for sale, apartments for rent, and property records</span><span class="listing-place"><svg width="7" height="10" viewBox="0 0 7 10"><path d="M3.5 0A3.5 3.5 0 0 0 0 3.5C0 6 3.5 10 3.5 10S7 6 7 3.5A3.5 3.5 0 0 0 3.5 0z" fill="#888"/></svg>Brooklandville, MD</span></div></article>
    <article class="listing"><div class="listing-photo" role="img" aria-label="Row of white glass-paned doors" style="background:linear-gradient(90deg,#e8e8e8,#c8c4bc 60%,#9a6a44)"></div><h3 class="listing-title">Finding the property you want</h3><div class="listing-meta"><span>Homes for sale, apartments for rent, and property records</span><span class="listing-place"><svg width="7" height="10" viewBox="0 0 7 10"><path d="M3.5 0A3.5 3.5 0 0 0 0 3.5C0 6 3.5 10 3.5 10S7 6 7 3.5A3.5 3.5 0 0 0 3.5 0z" fill="#888"/></svg>Brooklandville, MD</span></div></article>
    <article class="listing"><div class="listing-photo" role="img" aria-label="White villa with a pool under blue sky" style="background:linear-gradient(180deg,#4a7ac0,#e8e4da 45%,#cfc8b8 80%,#3a8ab0)"></div><h3 class="listing-title">Finding the property you want</h3><div class="listing-meta"><span>Homes for sale, apartments for rent, and property records</span><span class="listing-place"><svg width="7" height="10" viewBox="0 0 7 10"><path d="M3.5 0A3.5 3.5 0 0 0 0 3.5C0 6 3.5 10 3.5 10S7 6 7 3.5A3.5 3.5 0 0 0 3.5 0z" fill="#888"/></svg>Brooklandville, MD</span></div></article>
    <article class="listing"><div class="listing-photo" role="img" aria-label="Grey two-storey house with a front porch" style="background:linear-gradient(180deg,#d0d4d8,#7a808a 50%,#4a5a3a)"></div><h3 class="listing-title">Finding the property you want</h3><div class="listing-meta"><span>Homes for sale, apartments for rent, and property records</span><span class="listing-place"><svg width="7" height="10" viewBox="0 0 7 10"><path d="M3.5 0A3.5 3.5 0 0 0 0 3.5C0 6 3.5 10 3.5 10S7 6 7 3.5A3.5 3.5 0 0 0 3.5 0z" fill="#888"/></svg>Brooklandville, MD</span></div></article>
    <article class="listing"><div class="listing-photo" role="img" aria-label="Cream townhouses under a blue sky" style="background:linear-gradient(180deg,#6a9ad0,#e4dcc4 50%,#7a8a5a)"></div><h3 class="listing-title">Finding the property you want</h3><div class="listing-meta"><span>Homes for sale, apartments for rent, and property records</span><span class="listing-place"><svg width="7" height="10" viewBox="0 0 7 10"><path d="M3.5 0A3.5 3.5 0 0 0 0 3.5C0 6 3.5 10 3.5 10S7 6 7 3.5A3.5 3.5 0 0 0 3.5 0z" fill="#888"/></svg>Brooklandville, MD</span></div></article>
    <article class="listing"><div class="listing-photo" role="img" aria-label="Stucco house with garage and green lawn" style="background:linear-gradient(180deg,#7aa8d8,#b8a48a 50%,#5a8a3a)"></div><h3 class="listing-title">Finding the property you want</h3><div class="listing-meta"><span>Homes for sale, apartments for rent, and property records</span><span class="listing-place"><svg width="7" height="10" viewBox="0 0 7 10"><path d="M3.5 0A3.5 3.5 0 0 0 0 3.5C0 6 3.5 10 3.5 10S7 6 7 3.5A3.5 3.5 0 0 0 3.5 0z" fill="#888"/></svg>Brooklandville, MD</span></div></article>
    <article class="listing"><div class="listing-photo" role="img" aria-label="Modern white terrace overlooking a lawn and pool" style="background:linear-gradient(90deg,#7a9a4a,#dcdcd4 55%,#f2f2f0)"></div><h3 class="listing-title">Finding the property you want</h3><div class="listing-meta"><span>Homes for sale, apartments for rent, and property records</span><span class="listing-place"><svg width="7" height="10" viewBox="0 0 7 10"><path d="M3.5 0A3.5 3.5 0 0 0 0 3.5C0 6 3.5 10 3.5 10S7 6 7 3.5A3.5 3.5 0 0 0 3.5 0z" fill="#888"/></svg>Brooklandville, MD</span></div></article>
    <article class="listing"><div class="listing-photo" role="img" aria-label="Two-storey house at dusk under a deep blue sky" style="background:linear-gradient(180deg,#1a3a8a,#3a4a8a 40%,#b09070 65%,#2a2a20)"></div><h3 class="listing-title">Finding the property you want</h3><div class="listing-meta"><span>Homes for sale, apartments for rent, and property records</span><span class="listing-place"><svg width="7" height="10" viewBox="0 0 7 10"><path d="M3.5 0A3.5 3.5 0 0 0 0 3.5C0 6 3.5 10 3.5 10S7 6 7 3.5A3.5 3.5 0 0 0 3.5 0z" fill="#888"/></svg>Brooklandville, MD</span></div></article>
  </main>

  <section class="newsletter">
    <div class="newsletter-copy">
      <h2 class="newsletter-title">Newsletter Signup</h2>
      <p class="newsletter-sub">Get a recent update through your email</p>
    </div>
    <div class="newsletter-form">
      <div class="fields"><div class="field">Your name...</div><div class="field">Your e-mail address...</div></div>
      <div class="subscribe"><svg width="12" height="10" viewBox="0 0 12 10"><path d="M0 0l12 5-12 5 2-5z" fill="#fff"/></svg>Subscribe</div>
    </div>
  </section>

  <section class="affiliations" aria-label="Affiliations">
    <span class="badge"></span><span class="badge round"></span><span class="badge round"></span><span class="badge"></span><span class="badge"></span><span class="badge round"></span>
  </section>

  <footer class="site-footer">
    <ul class="footer-nav"><li>Home</li><li>Auctions</li><li>Appraisals</li><li>Real Estate</li><li>FAQ</li><li>About Us</li><li>Contact Us</li></ul>
    <p class="copyright">© Copyright 2013. Nerith. All rights reserved.</p>
  </footer>
</div>
</body>
</html>
```